Engagement party email invitation

I need an invitation designed for my upcoming engagement party. I would like the attached picture to be encircled by gum leaves or some sort of garland of green leaves.

Traditional text typeface eg Sackers Gothic Light or Mrs Eaves.

Thanks
Marnie

Font styles to use
Serif
Script

```html
<!DOCTYPE html>
<html lang="en">
<head>
<meta charset="utf-8">
<title>Engagement Party Invitation</title>
<link rel="stylesheet" href="https://fonts.googleapis.com/css2?family=Cormorant+Garamond:wght@500;600;700&display=swap">
<style>
  :root {
    --sky: #eef3f7;
    --haze: #dde6ee;
    --hill: #bcc8bc;
    --water: #c9dbe7;
    --water-deep: #b6cddd;
    --leaf-light: #a9d07a;
    --leaf: #78b04a;
    --leaf-deep: #3d8530;
    --gold: #9c6a1f;
    --gold-light: #e0ad55;
    --bronze: #8a6848;
    --band: rgba(255, 255, 255, 0.55);
  }
  * { margin: 0; padding: 0; box-sizing: border-box; }
  html, body { width: 1200px; height: 617px; overflow: hidden; background: #ffffff; }
  .invitation {
    position: relative;
    width: 1200px;
    height: 617px;
    overflow: hidden;
    font-family: "Cormorant Garamond", Georgia, serif;
  }
  .harbour-scene {
    position: absolute;
    inset: 0;
    background: linear-gradient(180deg, var(--sky) 0%, var(--haze) 26%, var(--hill) 40%, var(--water) 58%, var(--water-deep) 100%);
  }
  .details-band {
    position: absolute;
    left: 0; right: 0;
    top: 407px; height: 133px;
    background: var(--band);
  }
  .garland {
    position: absolute;
    inset: 0;
    width: 1200px;
    height: 617px;
  }
  .line {
    position: absolute;
    left: 0; right: 0;
    text-align: center;
    white-space: nowrap;
    line-height: 1;
  }
  .hosts, .invite-line, .event-details {
    color: var(--gold);
    font-weight: 600;
    text-shadow: 0 1px 0 var(--gold-light), 1px 2px 2px rgba(60, 35, 0, 0.5);
  }
  .hosts { top: 52px; font-size: 54px; letter-spacing: 2.5px; }
  .invite-line { top: 124px; font-size: 56px; letter-spacing: 3px; }
  .couple {
    top: 220px;
    font-size: 136px;
    font-weight: 500;
    letter-spacing: 3px;
    color: var(--bronze);
    text-shadow: 1px 1px 0 rgba(255, 240, 215, 0.85), -1px -1px 1px rgba(40, 25, 10, 0.6);
  }
  .event-details { font-size: 54px; letter-spacing: 1.5px; }
  .event-date { top: 410px; }
  .event-venue { top: 481px; }
</style>
</head>
<body>
  <main class="invitation">
    <div class="harbour-scene" role="img" aria-label="Soft watercolour view of a harbour with city skyline, wooded headland and moored boats"></div>
    <div class="details-band"></div>

    <svg class="garland" viewBox="0 0 1200 617" role="img" aria-label="Garland of gum leaves, ferns and small blue flowers framing the harbour view">
      <defs>
        <linearGradient id="leafTop" x1="0" y1="0" x2="1" y2="0">
          <stop offset="0" stop-color="var(--leaf-light)" stop-opacity="0.55"/>
          <stop offset="0.5" stop-color="var(--leaf)" stop-opacity="0.8"/>
          <stop offset="1" stop-color="var(--leaf-deep)" stop-opacity="0.85"/>
        </linearGradient>
        <linearGradient id="leafSide" x1="0" y1="0" x2="0" y2="1">
          <stop offset="0" stop-color="var(--leaf)" stop-opacity="0.8"/>
          <stop offset="1" stop-color="var(--leaf-light)" stop-opacity="0.6"/>
        </linearGradient>
        <linearGradient id="leafBottom" x1="0" y1="1" x2="1" y2="0">
          <stop offset="0" stop-color="var(--leaf-deep)" stop-opacity="0.85"/>
          <stop offset="0.6" stop-color="var(--leaf)" stop-opacity="0.65"/>
          <stop offset="1" stop-color="var(--leaf-light)" stop-opacity="0.45"/>
        </linearGradient>
      </defs>
      <path class="garland__top-right" fill="url(#leafTop)"
            d="M700 0 H1200 V420 C1170 400 1130 370 1110 330 C1090 280 1110 230 1060 200 C1010 170 960 150 930 110 C900 70 880 45 820 35 C770 28 720 20 700 0 Z"/>
      <path class="garland__right" fill="url(#leafSide)"
            d="M1200 240 V400 C1160 395 1120 370 1115 330 C1112 290 1150 255 1200 240 Z"/>
      <path class="garland__left" fill="url(#leafSide)"
            d="M0 220 C60 215 130 235 140 285 C148 330 100 355 40 350 C20 348 8 345 0 342 Z"/>
      <path class="garland__bottom-left" fill="url(#leafBottom)"
            d="M0 360 C40 365 80 380 100 410 C120 450 150 480 200 520 C260 545 330 530 400 545 C480 560 560 565 620 600 L630 617 H0 Z"/>
    </svg>

    <p class="line hosts">Catherine &amp; David Rowe</p>
    <p class="line invite-line">invite you to celebrate the engagement of</p>
    <h1 class="line couple">Marnie &amp; Thomas</h1>
    <p class="line event-details event-date">Saturday 23 January 2021, 6.30pm</p>
    <p class="line event-details event-venue">14 Harbour Lane, Riverside Point</p>
  </main>
</body>
</html>
```